Brookvane Consulting Business Card Design

Business Card Design for Brookvane Consulting. Brookvane Consulting is a boutique consultancy based in Atlanta, GA., that specializes in marketing strategy, organization planning, and leadership development. We provide solutions for small businesses and startups as well as Vantage 300 companies.

http://brookvaneconsulting.com/

Target Market(s)

We provide solutions for small businesses and startups as well as Vantage 300 companies.

Industry/Entity Type

Consulting

Contact Information for Business Card

Two sided business card with priority on contact information, logo, tag line (Guidance to Plan Better, Act Sooner, Grow Further)

Colors

Designer to choose colors to be used in the design.

Requirements
Must have
• contact information, logo, tag line (Guidance to Plan Better, Act Sooner, Grow Further)
• Simple no over communication.
Nice to have
• I would like to see different placements of logo and creative use of both sides of the card
Should not have
• Do not put too much information on the card.

```html
<!DOCTYPE html>
<html lang="en">
<head>
<meta charset="utf-8">
<title>Brookvane Consulting – Business Card</title>
<link rel="stylesheet" href="https://fonts.googleapis.com/css2?family=Roboto:wght@400;500&display=swap">
<style>
  :root {
    --backdrop: #5a5a5a;
    --card: #333333;
    --card-edge: #2a2a2a;
    --front-mark: #8a8a8a;
    --ink: #ffffff;
    --ink-soft: #e6e6e6;
  }
  * { margin: 0; padding: 0; box-sizing: border-box; }
  html, body {
    width: 799px;
    height: 1200px;
    overflow: hidden;
  }
  body {
    background: var(--backdrop);
    font-family: "Roboto", Arial, sans-serif;
    position: relative;
  }
  .card {
    position: absolute;
    left: 90px;
    width: 620px;
    height: 354px;
    background: var(--card);
    border-radius: 26px;
    box-shadow: 0 10px 24px rgba(0,0,0,0.45);
    border: 1px solid var(--card-edge);
  }
  .card--front { top: 110px; }
  .card--back { top: 700px; }

  .front-name {
    position: absolute;
    left: 0; right: 0;
    top: 140px;
    text-align: center;
    font-size: 44px;
    font-weight: 500;
    color: var(--front-mark);
    letter-spacing: 0.5px;
  }

  .back-brand {
    position: absolute;
    left: 36px;
    top: 40px;
  }
  .back-name {
    font-size: 34px;
    font-weight: 500;
    color: var(--ink);
    letter-spacing: 0.5px;
  }
  .tagline {
    margin-top: 8px;
    font-size: 13px;
    font-weight: 400;
    color: var(--ink-soft);
    letter-spacing: 0.3px;
  }

  .contact {
    position: absolute;
    left: 300px;
    top: 190px;
    color: var(--ink);
  }
  .contact-person {
    font-size: 22px;
    font-weight: 500;
    margin-bottom: 12px;
  }
  .contact-line {
    font-size: 15px;
    line-height: 22px;
    font-weight: 400;
  }
</style>
</head>
<body>
  <section class="card card--front" aria-label="Card front">
    <div class="front-name">Brookvane Consulting</div>
  </section>

  <section class="card card--back" aria-label="Card back">
    <div class="back-brand">
      <div class="back-name">Brookvane Consulting</div>
      <div class="tagline">Guidance to Plan Better, Act Sooner, Grow Further</div>
    </div>
    <div class="contact">
      <div class="contact-person">Dario</div>
      <div class="contact-line">555-013-2947</div>
      <div class="contact-line">dario@brookvaneconsulting.com</div>
      <div class="contact-line">www.brookvaneconsulting.com</div>
    </div>
  </section>
</body>
</html>
```